New Business Card Design Project

Need a design that will create an impact / strong impression towards our clients for our business. We are in the lighting business and we do lighting retrofits for large commercial to industrial clientele.

Target Market(s)

Lighting Industry

Industry/Entity Type

Business

Font styles to use
Other font styles liked:
• we would like to use the font on our logo, not sure what it is though..

Requirements
Must have
• Our logo.
Nice to have
• We are open to suggestions that have to do with lighting.

```html
<!DOCTYPE html>
<html lang="en">
<head>
<meta charset="utf-8">
<title>Brightline Retrofit Co. — Business Card</title>
<link href="https://fonts.googleapis.com/css2?family=Lato:wght@400;700&display=swap" rel="stylesheet">
<style>
  :root {
    --backdrop: #4a4a4a;
    --forest: #12390f;
    --deep: #0f3a10;
    --green: #0b7d2c;
    --leaf: #5cc25a;
    --paper: #ffffff;
    --ink: #1a1a1a;
  }
  html, body {
    margin: 0;
    padding: 0;
    width: 1200px;
    height: 900px;
    overflow: hidden;
    background: var(--backdrop);
    font-family: "Lato", sans-serif;
  }
  .canvas {
    position: relative;
    width: 1200px;
    height: 900px;
  }
  .card {
    position: absolute;
    width: 700px;
    height: 400px;
    box-shadow: 0 10px 24px rgba(0,0,0,.45);
    overflow: hidden;
  }
  /* Front */
  .card-front {
    left: 420px;
    top: 40px;
    background: var(--forest);
    color: var(--paper);
  }
  .front-brand {
    position: absolute;
    left: 0; right: 0;
    top: 140px;
    display: flex;
    justify-content: center;
    align-items: center;
    gap: 16px;
  }
  .brand-mark {
    width: 26px;
    height: 26px;
    background: var(--leaf);
  }
  .brand-name {
    font-weight: 700;
    font-size: 40px;
    letter-spacing: 1px;
  }
  .front-web {
    position: absolute;
    left: 0; right: 0;
    bottom: 56px;
    text-align: center;
    font-size: 20px;
    letter-spacing: 1.5px;
  }
  /* Back */
  .card-back {
    left: 120px;
    top: 460px;
    background: var(--paper);
    color: var(--ink);
  }
  .back-brand {
    position: absolute;
    left: 44px;
    top: 46px;
    display: flex;
    align-items: center;
    gap: 14px;
    color: var(--deep);
  }
  .back-brand .brand-mark { background: var(--green); }
  .back-brand .brand-name { font-size: 36px; }
  .divider {
    position: absolute;
    left: 44px;
    right: 44px;
    top: 150px;
    height: 2px;
    background: var(--green);
  }
  .contacts {
    position: absolute;
    left: 44px;
    top: 176px;
    list-style: none;
    margin: 0;
    padding: 0;
    font-size: 21px;
    line-height: 31px;
  }
  .contacts li { display: flex; align-items: center; gap: 12px; }
  .contacts svg { width: 18px; height: 18px; fill: var(--green); }
  .person {
    position: absolute;
    right: 44px;
    top: 168px;
    text-align: right;
  }
  .person-name {
    color: var(--green);
    font-weight: 700;
    font-size: 32px;
    margin: 0;
  }
  .person-role {
    font-size: 21px;
    margin: 2px 0 0;
  }
  .address {
    position: absolute;
    right: 44px;
    top: 262px;
    text-align: right;
    font-size: 21px;
    line-height: 28px;
    font-style: normal;
  }
  .wave-band {
    position: absolute;
    left: 0;
    bottom: 0;
    width: 700px;
    height: 120px;
  }
  .back-web {
    position: absolute;
    left: 200px;
    bottom: 30px;
    color: var(--paper);
    font-size: 22px;
    letter-spacing: .5px;
  }
</style>
</head>
<body>
<main class="canvas">

  <section class="card card-front" aria-label="Card front">
    <div class="front-brand">
      <span class="brand-mark"></span>
      <span class="brand-name">Brightline Retrofit Co.</span>
    </div>
    <div class="front-web">www.brightline-retrofit.com</div>
  </section>

  <section class="card card-back" aria-label="Card back">
    <div class="back-brand">
      <span class="brand-mark"></span>
      <span class="brand-name">Brightline Retrofit Co.</span>
    </div>

    <div class="divider"></div>

    <ul class="contacts">
      <li>
        <svg viewBox="0 0 24 24" aria-hidden="true"><path d="M6.6 10.8a15 15 0 0 0 6.6 6.6l2.2-2.2c.3-.3.7-.4 1-.2 1.1.4 2.3.6 3.6.6.6 0 1 .4 1 1V20c0 .6-.4 1-1 1A17 17 0 0 1 3 4c0-.6.4-1 1-1h3.5c.6 0 1 .4 1 1 0 1.3.2 2.5.6 3.6.1.3 0 .7-.2 1z"/></svg>
        (555) 014-2200
      </li>
      <li>
        <svg viewBox="0 0 24 24" aria-hidden="true"><path d="M6 2h12v5H6zM4 8h16a2 2 0 0 1 2 2v7h-4v5H6v-5H2v-7a2 2 0 0 1 2-2zm4 8v4h8v-4z"/></svg>
        (555) 014-2201
      </li>
      <li>
        <svg viewBox="0 0 24 24" aria-hidden="true"><path d="M2 5h20v14H2zm2 2v.5l8 5 8-5V7zm0 2.8V17h16V9.8l-8 5z"/></svg>
        info@brightline-retrofit.com
      </li>
    </ul>

    <div class="person">
      <p class="person-name">Mark Ellison</p>
      <p class="person-role">Manager</p>
    </div>

    <address class="address">
      1480 North Elm Avenue<br>
      Fairview, IL 60999
    </address>

    <svg class="wave-band" viewBox="0 0 700 120" preserveAspectRatio="none" aria-hidden="true">
      <path d="M0 10 C 220 10, 480 40, 700 110 L700 120 L0 120 Z" fill="var(--green)"/>
      <path d="M0 18 C 220 18, 470 52, 700 116 L700 120 L0 120 Z" fill="var(--paper)"/>
      <path d="M0 24 C 220 24, 460 64, 700 120 L0 120 Z" fill="var(--deep)"/>
    </svg>
    <div class="back-web">www.brightline-retrofit.com</div>
  </section>

</main>
</body>
</html>
```